Fitness Equipment & Service

I want to make the card eye catching and fun. We are called Corvane Motion Limited and we are based in Wales. We sell, install and service all types of fitness equipment from Skipping ropes, right through the Dumbbells, Kettle bells and Barbells through to state of the art Treadmills, Running Machines and Strength Equipment. We also design and install changing room furniture and lockers.

TYPOGRAPHY
We would like to use Futrura. Futura has an appearance of efficiency and forwardness. The typeface is derived
from simple geometric forms (near-perfect circles, triangles and squares) and is based on strokes of
near-even weight, which are low in contrast. This is most visible in the almost perfectly round stroke of
the o, which is nonetheless slightly ovoid.
The lowercase has tall ascenders, which rise above the cap line. The uppercase
characters present proportions similar to those of classical Roman capitals.

TYPOGRAPHIC CONSIDERATIONS
No Strike though
No Horizontal Scaling
No Drop Shadows
No Effects
Never use less than 120% Leading

OUR CORPORATE COLOURS
BRAND GUIDELINES
We were thinking that our primary colour palette consists of the Acid Green (Pantone 382) and Process Black.

We work closely with tquarly Ltd and would like to include their name on the card somewhere. I have attached images of the other brands that we work with as an idea or the small icons I have included that illustrate what we do?. I have very kindly been given permission to use any of the images off the files that I have included below, so I hope these help. I will include these below. I would be open to suggestions if it made the card more striking Can you do it?
Updates

Hi All, Just wanted to add a few thoughts but you are the guys with the creative visions (thats why are here) We are based in Wales, UK and we would be open to lots of different ideas on a theme but must be eye catching, Bold and FUN. If you can or think that the Welsh or any dragon could be put in there then go for it (its not a must have) We have also added some ideas for colour but again its over to you!! GO FOR IT ! Thanks and look forward to your visions! Owen

Hi All, Just thought I would sen through the contact details that need to be on the card. (if you want to play around with icons instead of the wording twitter, Facebook, go for it): Corvane Motion Limited Owen Pritchard Managing Director Mob: +44 (0)7582 913 406 e-mail: sales@corvanemotion.co.uk Web: Corvanemotion.co.uk twitter: @motionLetterbin Facebook: Corvane Motion Limited

```html
<!DOCTYPE html>
<html lang="en">
<head>
<meta charset="utf-8">
<title>Corvane Motion Limited – Business Card</title>
<link rel="stylesheet" href="https://fonts.googleapis.com/css2?family=Arimo:wght@700&family=Open+Sans:wght@400;600&display=swap">
<style>
  :root {
    --page: #ebe8e4;
    --navy: #26447f;
    --ink: #14193a;
    --white: #ffffff;
    --tile-blue: #1a63b1;
    --tile-cyan: #35c2ef;
    --tile-deep: #0f3f6f;
    --tile-grey: #7a98aa;
    --tile-mist: #afc4d0;
    --tile-night: #0b2747;
  }
  * { margin: 0; padding: 0; box-sizing: border-box; }
  html, body {
    width: 1189px; height: 1200px; overflow: hidden;
    background: var(--page);
    font-family: "Open Sans", Arial, sans-serif;
  }
  .canvas { position: relative; width: 1189px; height: 1200px; }

  .card {
    position: absolute; left: 140px; width: 917px; height: 524px;
    overflow: hidden; background: var(--white);
  }
  .card--front { top: 45px; }
  .card--back { top: 624px; height: 523px; background: var(--tile-blue); }

  .front-wave { position: absolute; inset: 0; }

  .brand-mark {
    position: absolute; left: 112px; top: 62px;
    width: 150px; height: 150px; border-radius: 50%;
    background: var(--navy);
  }
  .brand-name {
    position: absolute; left: 61px; top: 238px; width: 260px;
    font-weight: 600; font-size: 27px; line-height: 1.2;
    color: var(--ink); text-align: center;
  }

  .holder { position: absolute; right: 48px; top: 232px; text-align: right; color: var(--white); }
  .holder__name { font-family: "Arimo", Arial, sans-serif; font-weight: 700; font-size: 42px; line-height: 1.2; }
  .holder__role { font-size: 28px; line-height: 1.2; }

  .contact { position: absolute; color: var(--white); font-size: 24px; line-height: 40px; }
  .contact--direct { right: 48px; top: 376px; text-align: right; }
  .contact--social { left: 33px; top: 417px; }
  .contact__row { display: flex; align-items: center; gap: 17px; }
  .contact--direct .contact__row { justify-content: flex-end; }
  .contact__icon { width: 21px; height: 21px; flex: none; }
  .contact__square { width: 21px; height: 21px; background: var(--white); flex: none; }

  .tile { position: absolute; }
  .name-band {
    position: absolute; left: 319px; top: 175px; width: 598px; height: 150px;
    background: var(--tile-deep);
    display: flex; align-items: center; justify-content: center;
  }
  .name-band__text {
    color: var(--white); font-weight: 600; font-size: 40px; line-height: 1.2;
    letter-spacing: 2px; text-align: center;
  }
</style>
</head>
<body>
<div class="canvas">

  <section class="card card--front">
    <svg class="front-wave" viewBox="0 0 917 524" width="917" height="524" aria-hidden="true">
      <path d="M0,368 C230,318 400,290 560,190 C700,105 820,96 917,104 L917,524 L0,524 Z" fill="var(--navy)"/>
      <path d="M0,378 C230,328 400,300 560,200 C700,115 820,106 917,114" fill="none" stroke="var(--white)" stroke-width="4"/>
    </svg>

    <div class="brand-mark"></div>
    <div class="brand-name">Corvane Motion<br>Limited</div>

    <div class="holder">
      <div class="holder__name">Owen Pritchard</div>
      <div class="holder__role">Managing Director</div>
    </div>

    <div class="contact contact--direct">
      <div class="contact__row">+44 (0)7582 913 406
        <svg class="contact__icon" viewBox="0 0 21 21" aria-hidden="true"><rect width="21" height="21" fill="#fff"/><rect x="6" y="3" width="9" height="15" rx="1.5" fill="var(--navy)"/><rect x="7.5" y="5" width="6" height="6" fill="#fff"/></svg>
      </div>
      <div class="contact__row">sales@corvanemotion.co.uk
        <svg class="contact__icon" viewBox="0 0 21 21" aria-hidden="true"><rect width="21" height="21" fill="#fff"/><rect x="3" y="5" width="15" height="11" fill="var(--navy)"/><path d="M3.5,5.5 L10.5,11 L17.5,5.5" fill="none" stroke="#fff" stroke-width="1.4"/></svg>
      </div>
      <div class="contact__row">Corvanemotion.co.uk
        <svg class="contact__icon" viewBox="0 0 21 21" aria-hidden="true"><rect width="21" height="21" fill="#fff"/><circle cx="10.5" cy="10.5" r="7" fill="var(--navy)"/><circle cx="10.5" cy="10.5" r="7" fill="none" stroke="#fff" stroke-width="0"/><path d="M3.5,10.5 H17.5 M10.5,3.5 V17.5" stroke="#fff" stroke-width="1.2"/></svg>
      </div>
    </div>

    <div class="contact contact--social">
      <div class="contact__row"><span class="contact__square"></span>@motionLetterbin</div>
      <div class="contact__row"><span class="contact__square"></span>Corvane Motion Limited</div>
    </div>
  </section>

  <section class="card card--back">
    <div class="tile" style="left:0;top:0;width:176px;height:175px;background:var(--tile-blue)" role="img" aria-label="Sunbed icon"></div>
    <div class="tile" style="left:176px;top:0;width:143px;height:175px;background:var(--tile-cyan)" role="img" aria-label="Exercise bike icon"></div>
    <div class="tile" style="left:319px;top:0;width:142px;height:175px;background:linear-gradient(120deg,var(--tile-blue) 45%,var(--tile-night))" role="img" aria-label="Dumbbell photograph"></div>
    <div class="tile" style="left:461px;top:0;width:142px;height:175px;background:var(--tile-deep)" role="img" aria-label="Locker icon"></div>
    <div class="tile" style="left:603px;top:0;width:143px;height:175px;background:var(--tile-blue)" role="img" aria-label="Weight bench icon"></div>
    <div class="tile" style="left:746px;top:0;width:171px;height:175px;background:linear-gradient(160deg,var(--tile-blue) 35%,var(--tile-night))" role="img" aria-label="Weight plate photograph"></div>

    <div class="tile" style="left:0;top:175px;width:176px;height:150px;background:var(--tile-blue)" role="img" aria-label="Fitness equipment photograph"></div>
    <div class="tile" style="left:176px;top:175px;width:143px;height:150px;background:var(--tile-grey)" role="img" aria-label="Kettlebell icon"></div>
    <div class="name-band"><div class="name-band__text">CORVANE MOTION<br>LIMITED</div></div>

    <div class="tile" style="left:0;top:325px;width:176px;height:148px;background:var(--tile-deep)" role="img" aria-label="Skipping rope icon"></div>
    <div class="tile" style="left:176px;top:325px;width:143px;height:148px;background:var(--tile-blue)" role="img" aria-label="Drink and apple icon"></div>
    <div class="tile" style="left:319px;top:325px;width:142px;height:148px;background:var(--tile-mist)" role="img" aria-label="Scales icon"></div>
    <div class="tile" style="left:461px;top:325px;width:142px;height:148px;background:linear-gradient(200deg,var(--tile-night),var(--tile-blue) 55%)" role="img" aria-label="Dumbbell photograph"></div>
    <div class="tile" style="left:603px;top:325px;width:143px;height:148px;background:var(--tile-blue)" role="img" aria-label="Boxing gloves icon"></div>
    <div class="tile" style="left:746px;top:325px;width:171px;height:148px;background:var(--tile-night)" role="img" aria-label="Weight plate photograph"></div>

    <div class="tile" style="left:0;top:473px;width:461px;height:50px;background:var(--tile-blue)"></div>
    <div class="tile" style="left:461px;top:473px;width:142px;height:50px;background:var(--tile-grey)"></div>
    <div class="tile" style="left:603px;top:473px;width:143px;height:50px;background:var(--tile-blue)"></div>
    <div class="tile" style="left:746px;top:473px;width:171px;height:50px;background:var(--tile-deep)"></div>
  </section>

</div>
</body>
</html>
```